Design website for new email startup

We are starting a company called Pingo.QZ (it will live at http://pingo.qz).

We would like the main landing page for our site designed. We have provided a very simple wireframe to help provide direction for the content it should include, but we do not expect the designers to adhere to it at all - we encourage unique ideas. There is some sample text in the wireframe - this does not have to be used, but may provide ideas.

We provide an easy way for people to manage email for a custom domain name. For example if you own "yourhouseword.example" you can point your DNS records to us and we'll make it easy to have emails addressed to your domain get forwarded to your existing email (gmail, etc). Folks running blogs, and other small sites can quickly setup email addresses for their domains and manage them in one place.

(For technical folks, we have you point your dns mx records to us, hence the name. That way all your email hits us and we can redirect it wherever you want. We make it easy to manage a single domain or a bunch of domains. Many domain registrars offer this service for a fee, and have clumsy management tools. We provide a robust simple toolset for free, as well as premium options).

The goal of the landing page is to get folks into the signup flow. The second priority flow is to have them take a look at the premium plan offerings.

We may offer the winning designer additional work for the remainder of the site design.
Updates

I've changed this project to a committed payment.  It is no longer refundable.  Thank you.

Target Market(s)

Bloggers, podcasters, designers, app developers - people who are a little tech savvy.

Industry/Entity Type

It Company

Font styles to use
Sans Serif

Colors

Designer to choose colors to be used in the design.

Requirements
Must have
• A full fidelity mockup (comp) of the landing page including the source file (psd, ai, etc).

Some sort of logo treatment for the pingo.qz brand

A call to action for signup, such as the suggested 'Get Started Here'
Nice to have
• A hip startup feel

Incorporation of the email theme

Give the impression it is simple, easy and fast

```html
<!DOCTYPE html>
<html lang="en">
<head>
<meta charset="utf-8">
<title>Pingo.qz — Email for your domain</title>
<link href="https://fonts.googleapis.com/css2?family=Open+Sans:wght@300;400;600&display=swap" rel="stylesheet">
<style>
:root{
  --green:#7f9a26;
  --green-dark:#5f7a16;
  --yellow:#f2c230;
  --header-bg:#f7f7f7;
  --page-bg:#f2f2f2;
  --ink:#222;
  --brand-ink:#333;
  --body-text:#555;
  --hero-bg:#000;
  --footer-bg:#0a0a0a;
  --icon-dark:#3d3d3d;
}
*{margin:0;padding:0;box-sizing:border-box}
html,body{width:1200px;height:953px;overflow:hidden}
body{font-family:"Open Sans",Arial,sans-serif;background:var(--page-bg);color:var(--ink);position:relative}

.site-header{position:absolute;left:0;top:0;width:1200px;height:111px;background:var(--header-bg);border-bottom:1px solid #e6e6e6}
.brand{position:absolute;left:124px;top:34px;display:flex;align-items:center;gap:12px}
.brand-mark{width:30px;height:30px;border-radius:50%;background:var(--green)}
.brand-name{font-size:34px;font-weight:400;color:var(--brand-ink);line-height:40px}
.social{position:absolute;left:974px;top:38px;display:flex;gap:3px}
.social span{width:36px;height:36px;border-radius:50%;display:block}
.social .s1{background:#0b78b5}.social .s2{background:#5a9ad6}.social .s3{background:#3b5998}

.main-nav{position:absolute;left:0;top:111px;width:1200px;height:39px;background:linear-gradient(#ffffff,#ebebeb);border-bottom:1px solid #d8d8d8}
.nav-list{position:absolute;left:112px;top:0;display:flex;list-style:none;height:39px}
.nav-list li{height:39px;line-height:41px;font-size:16px;color:#111;text-align:center;border-right:1px solid #dcdcdc}
.nav-list li:nth-child(1){width:124px}
.nav-list li:nth-child(2){width:123px}
.nav-list li:nth-child(3){width:123px}
.search{position:absolute;left:866px;top:7px;width:224px;height:26px;background:#fff;border:1px solid #dcdcdc;font-size:10px;font-style:italic;color:#777;padding:5px 8px}
.search svg{position:absolute;right:10px;top:5px}

.hero{position:absolute;left:0;top:150px;width:1200px;height:438px;background:var(--hero-bg);overflow:hidden}
.hero-visual{position:absolute;left:560px;top:0;width:640px;height:438px;
  background:radial-gradient(ellipse at 45% 30%,rgba(70,160,240,.75),rgba(20,50,90,.6) 40%,rgba(0,0,0,0) 75%),linear-gradient(90deg,#000 0%,#0c1a2c 25%,#1b2c44 60%,#26364c 100%)}
.hero-copy{position:absolute;left:113px;top:103px;width:440px;font-size:24px;font-weight:300;line-height:34px;color:#fff;white-space:nowrap}
.hero-copy strong{color:var(--green);font-weight:600}
.cta{position:absolute;top:268px;height:37px;line-height:37px;font-size:15px;text-align:center}
.cta-primary{left:110px;width:165px;background:linear-gradient(var(--green),var(--green-dark));color:#fff}
.cta-secondary{left:280px;width:165px;background:var(--yellow);color:#111}
.slider-dots{position:absolute;left:113px;top:401px;display:flex;gap:4px}
.slider-dots span{width:13px;height:13px;border-radius:50%;background:#666}
.slider-dots span.active{background:#9bbb22}

.feature{position:absolute;top:687px;width:460px;height:141px;background:#fff;border:1px solid #dedede;text-align:center;box-shadow:8px 10px 10px -6px rgba(0,0,0,.18)}
.feature-left{left:130px}
.feature-right{left:617px}
.feature-icon{position:absolute;left:50%;top:-45px;margin-left:-36px;width:72px;height:72px;border-radius:50%;background:#fff;display:flex;align-items:center;justify-content:center}
.feature-title{margin-top:22px;font-size:20px;line-height:24px;font-weight:400;white-space:nowrap}
.feature-left .feature-title{color:var(--green)}
.feature-right .feature-title{color:#333}
.feature-text{margin-top:8px;font-size:11.5px;line-height:18px;color:var(--body-text);white-space:nowrap}

.site-footer{position:absolute;left:0;top:897px;width:1200px;height:56px;background:var(--footer-bg);color:#fff;font-size:13px;text-align:center;line-height:54px}
</style>
</head>
<body>
<header class="site-header">
  <div class="brand"><span class="brand-mark"></span><span class="brand-name">Pingo.qz</span></div>
  <div class="social" aria-label="Social links"><span class="s1"></span><span class="s2"></span><span class="s3"></span></div>
</header>

<nav class="main-nav">
  <ul class="nav-list"><li>How It Works</li><li>Support</li><li>Login</li></ul>
  <div class="search">Enter your search
    <svg width="16" height="16" viewBox="0 0 16 16"><circle cx="6.5" cy="6.5" r="5" fill="none" stroke="#bbb" stroke-width="2"/><line x1="10" y1="10" x2="15" y2="15" stroke="#bbb" stroke-width="2.5"/></svg>
  </div>
</nav>

<section class="hero">
  <div class="hero-visual" role="img" aria-label="Businessman touching a glowing interface of web and business icons"></div>
  <p class="hero-copy"><strong>Choosing</strong> and registeringa<br>great domain name is one of the first<br>steps towards building a successful<br>internet presence.</p>
  <div class="cta cta-primary">GET STARTED FREE</div>
  <div class="cta cta-secondary">COMPARE PLANS</div>
  <div class="slider-dots"><span class="active"></span><span></span><span></span></div>
</section>

<article class="feature feature-left">
  <div class="feature-icon">
    <svg width="60" height="60" viewBox="0 0 60 60"><circle cx="30" cy="30" r="30" fill="var(--green)"/><g fill="none" stroke="#fff" stroke-width="2.5"><circle cx="30" cy="30" r="18"/><ellipse cx="30" cy="30" rx="8" ry="18"/><line x1="12" y1="30" x2="48" y2="30"/><path d="M15 21h30M15 39h30"/></g></svg>
  </div>
  <h2 class="feature-title">Configure your SkyShield<br>DNS to use pingo.qz</h2>
  <p class="feature-text">Lorem ipsum dolor sit amet, consectetur adipisicing<br>elit, sed do eiusmod tempor incididunt ut labore et<br>dolore magna aliqua. Ut enim ad minim veniam, quis</p>
</article>

<article class="feature feature-right">
  <div class="feature-icon">
    <svg width="60" height="60" viewBox="0 0 60 60"><circle cx="30" cy="30" r="30" fill="var(--icon-dark)"/><g fill="none" stroke="#fff" stroke-width="2.5"><circle cx="28" cy="28" r="16"/><ellipse cx="28" cy="28" rx="7" ry="16"/><line x1="12" y1="28" x2="44" y2="28"/></g><path d="M36 34v14h10v-8l-6-2v-4z" fill="#fff"/></svg>
  </div>
  <h2 class="feature-title">Pingo.qz with your DomainNest domain<br>registraton for reliable email forwarding</h2>
  <p class="feature-text">Lorem ipsum dolor sit amet, consectetur adipisicing elit,<br>sed do eiusmod tempor incididunt ut labore et<br>magna aliqua. Ut enim ad minim veniam, quis nostrud.</p>
</article>

<footer class="site-footer">Copyright © 2014, Pingo.qz All Rights Reserved.</footer>
</body>
</html>
```